Hacienda Monte Verda Business cards

We would like 3 individual business cards with the logo you designed:

1) Marta Pellingford - Phone: 206 555 0147
2) Theodore R Pellingford - Phone 206 555 0183
3) Dana Moreth - Phone 310-555-0162

Address for all three cards:
7218 142nd Ave NE
Brindle Hollow, WA 98000
HaciendaMonteVerda@brindlemail.com

```html
<!DOCTYPE html>
<html lang="en">
<head>
<meta charset="utf-8">
<title>Hacienda Monte Verda – Business Card</title>
<link rel="stylesheet" href="https://fonts.googleapis.com/css2?family=Didact+Gothic&family=Montserrat:wght@700&display=swap">
<style>
  :root {
    --page-bg: #e4e4e2;
    --card-light: #ffffff;
    --card-shade: #dcdcdc;
    --ink: #1b1b1b;
    --ink-soft: #333333;
    --art-dark: #2a2a2a;
    --art-mid: #6a6a6a;
  }
  * { box-sizing: border-box; margin: 0; padding: 0; }
  html, body {
    width: 1200px; height: 871px; overflow: hidden;
    background: var(--page-bg);
  }
  .canvas {
    position: relative; width: 1200px; height: 871px;
  }
  .business-card {
    position: absolute; left: 100px; top: 150px;
    width: 1000px; height: 571px;
    background: linear-gradient(160deg, var(--card-light) 0%, #f4f4f4 45%, var(--card-shade) 100%);
    box-shadow: 0 10px 30px rgba(0,0,0,0.18);
    font-family: "Didact Gothic", "Century Gothic", sans-serif;
    color: var(--ink);
  }
  .brand-art {
    position: absolute; left: 150px; top: 110px;
    width: 290px; height: 190px;
    background: radial-gradient(ellipse at 35% 40%, var(--art-dark) 0%, var(--art-mid) 60%, rgba(106,106,106,0) 100%);
  }
  .brand-name {
    position: absolute; left: 80px; top: 318px; width: 430px;
    text-align: center; font-size: 38px; letter-spacing: 1px;
    color: var(--ink); white-space: nowrap;
  }
  .contact {
    position: absolute; left: 560px; top: 140px;
  }
  .holder-name {
    font-family: "Montserrat", Arial, sans-serif; font-weight: 700;
    font-size: 26px; margin-bottom: 34px; margin-left: 4px;
  }
  .contact-row {
    display: flex; align-items: flex-start; gap: 22px;
    font-size: 19px; line-height: 35px; color: var(--ink-soft);
    margin-bottom: 12px; white-space: nowrap;
  }
  .contact-row svg { flex: none; width: 26px; height: 26px; margin-top: 5px; }
</style>
</head>
<body>
<div class="canvas">
  <div class="business-card">
    <div class="brand-art" role="img" aria-label="Silhouette of a large tree above a fence with horses and birds"></div>
    <div class="brand-name">Hacienda Monte Verda</div>

    <div class="contact">
      <div class="holder-name">Marta Pellingford</div>

      <div class="contact-row">
        <svg viewBox="0 0 24 24" fill="none" stroke="#1b1b1b" stroke-width="1.6" aria-hidden="true">
          <rect x="7" y="2.5" width="10" height="19" rx="2"/>
          <line x1="10.5" y1="18" x2="13.5" y2="18"/>
        </svg>
        <span>206 555 0147</span>
      </div>

      <div class="contact-row">
        <svg viewBox="0 0 24 24" fill="none" stroke="#1b1b1b" stroke-width="1.6" aria-hidden="true">
          <path d="M12 21.5s-6.5-7-6.5-11.5a6.5 6.5 0 0 1 13 0c0 4.5-6.5 11.5-6.5 11.5z"/>
          <circle cx="12" cy="10" r="2.3"/>
        </svg>
        <span>Address for all three cards:<br>7218 142nd Ave NE<br>Brindle Hollow, WA 98000</span>
      </div>

      <div class="contact-row">
        <svg viewBox="0 0 24 24" fill="none" stroke="#1b1b1b" stroke-width="1.6" aria-hidden="true">
          <rect x="3" y="6" width="18" height="12.5"/>
          <path d="M3 6l9 7 9-7"/>
        </svg>
        <span>HaciendaMonteVerda@brindlemail.com</span>
      </div>
    </div>
  </div>
</div>
</body>
</html>
```